Laser Tattoo Removal Business Cards

We are looking for a professional business card design for a laser tattoo removal business. Ideally looking for a black business card design. The name of the business is Brightline Tattoo Removal. We place our cards at local tattoo shops so we ideally are looking for something trendy/edgy to draw both male and female clientele in.

Target Market(s)

Male/Female ages 18-60

Contact Information for Business Card

black background ideally.. hoping to stay within greys, whites and black

Font styles to use
Serif
Sans Serif

Colors
121212
a9a9a9
5c5c5c
f5f5f5
ffffff
7f7f7f
606060
848484
9d9d9d

Requirements
Must have
• Employee Info:
• Melissa Thornbury
• Chief Executive Offer
• m: 919.537.2846
• w: 919.362.4178
• f: 919.685.3907
• mthornbury@brightlinetattooremoval.example
• Address:
• 4615 Oakmere Pkwy, Suite 210
• Raleigh, NC 27654
• Website:
• www.brightlinetattooremoval.example
Nice to have
• Myabe business name on back or logo on back and employee info on the front

```html
<!DOCTYPE html>
<html lang="en">
<head>
<meta charset="utf-8">
<title>Brightline Tattoo Removal – Business Cards</title>
<link rel="stylesheet" href="https://fonts.googleapis.com/css2?family=Oswald:wght@400;500&family=Roboto+Condensed:wght@400&family=Mulish:wght@400;500;700;800&display=swap">
<style>
  :root {
    --ink: #121212;
    --band: #262626;
    --grey-dark: #5c5c5c;
    --grey-mid: #7f7f7f;
    --grey-soft: #a9a9a9;
    --paper: #f5f5f5;
    --white: #ffffff;
    --stage-light: #d2d2d2;
    --stage-dark: #868686;
  }
  * { margin: 0; padding: 0; box-sizing: border-box; }
  html, body { width: 1200px; height: 960px; overflow: hidden; }
  body {
    position: relative;
    background: linear-gradient(90deg, var(--stage-light), var(--stage-dark));
    font-family: "Mulish", sans-serif;
  }
  .card {
    position: absolute;
    width: 600px;
    height: 343px;
    overflow: hidden;
  }
  /* Front */
  .card-front { left: 302px; top: 122px; background: var(--white); }
  .front-pattern {
    position: absolute; inset: 0;
    background: linear-gradient(180deg, #f7f7f7, #eeeeee);
  }
  .identity {
    position: absolute; left: 0; right: 0; top: 44px;
    text-align: center; transform: translateX(-9px);
  }
  .person-name {
    font-family: "Oswald", sans-serif; font-weight: 400;
    font-size: 36px; line-height: 40px; color: var(--ink);
    transform: scaleX(0.86); letter-spacing: 0.5px;
  }
  .person-email {
    font-family: "Roboto Condensed", sans-serif;
    font-size: 12.5px; color: var(--grey-mid); margin-top: 2px;
    text-transform: uppercase;
  }
  .person-title {
    font-size: 13px; font-weight: 700; color: var(--grey-mid);
    letter-spacing: 0.6px; margin-top: 4px;
  }
  .contact-band {
    position: absolute; left: 0; right: 0; top: 146px; height: 113px;
    background: var(--band); color: var(--white);
    font-size: 13.5px; line-height: 18px;
  }
  .phones { position: absolute; right: 322px; top: 29px; text-align: right; }
  .band-divider {
    position: absolute; left: 295px; top: 30px; width: 1px; height: 50px;
    background: var(--grey-soft);
  }
  .address { position: absolute; left: 313px; top: 29px; }
  .website {
    position: absolute; left: 0; right: 0; top: 292px;
    text-align: center; font-size: 14px; letter-spacing: 1px;
    color: var(--grey-dark);
  }
  .website strong { font-weight: 800; color: var(--grey-dark); }
  /* Back */
  .card-back { left: 299px; top: 495px; background: var(--ink); }
  .back-pattern {
    position: absolute; inset: 0;
    background: radial-gradient(ellipse at 50% 45%, #2a2a2a 0%, #1a1a1a 55%, #121212 100%);
  }
  .brand-name {
    position: absolute; left: 0; right: 0; top: 108px;
    text-align: center; color: #e4e4e4;
    font-family: "Oswald", sans-serif; font-weight: 400;
  }
  .brand-name .brand-main { display: block; font-size: 50px; line-height: 58px; letter-spacing: 3px; }
  .brand-name .brand-sub { display: block; font-size: 19px; line-height: 30px; letter-spacing: 4px; margin-top: 8px; }
</style>
</head>
<body>
  <section class="card card-front">
    <div class="front-pattern" role="img" aria-label="Light grey damask pattern background"></div>
    <div class="identity">
      <h1 class="person-name">MELISSA THORNBURY</h1>
      <p class="person-email">mthornbury@brightlinetattooremoval.example</p>
      <p class="person-title">CHIEF EXECUTIVE OFFER</p>
    </div>
    <div class="contact-band">
      <div class="phones">
        <p>(m) 919.537.2846</p>
        <p>(w) 919.362.4178</p>
        <p>(f) 919.685.3907</p>
      </div>
      <div class="band-divider"></div>
      <div class="address">
        <p>4615 Oakmere Pkwy</p>
        <p>Suite 210</p>
        <p>Raleigh, NC 27654</p>
      </div>
    </div>
    <p class="website">www.<strong>BRIGHTLINETATTOOREMOVAL</strong>.example</p>
  </section>

  <section class="card card-back">
    <div class="back-pattern" role="img" aria-label="Dark damask pattern background"></div>
    <p class="brand-name">
      <span class="brand-main">BRIGHTLINE</span>
      <span class="brand-sub">TATTOO REMOVAL</span>
    </p>
  </section>
</body>
</html>
```